Zestora - Landing Page

Need a landing page for a journal app. The app is based on a retrospective board, where each journal entry is split into 3 sections: "What went well", "What Didn't Go Well" and "Things To Try".
The landing page should match the style of all modern web application landing pages. Think Brint, Tivalo, Mirvane. I've included screenshots of the app.
One feature that I want to highlight that is not ready yet, is an AI coach. It will offer insights based on the history of the user's journal entries
1 page

```html
<!DOCTYPE html>
<html lang="en">
<head>
<meta charset="utf-8">
<title>Zestora – Journal your days, retrospective style</title>
<link rel="stylesheet" href="https://fonts.googleapis.com/css2?family=Poppins:wght@600;700&family=Roboto:wght@400;500;700&display=swap">
<style>
:root{
  --blue:#0b57b7;
  --blue-deep:#0747a0;
  --blue-soft:#c7d6ec;
  --ink:#1c1c1c;
  --text:#4a4a4a;
  --muted:#8a8f98;
  --line:#e4e7ec;
  --navy:#1f2a37;
  --green:#2ec27e;
  --white:#fff;
  --dots:#dfe6f1;
}
*{box-sizing:border-box;margin:0;padding:0}
html,body{width:1200px;height:3994px;overflow:hidden}
body{position:relative;background:var(--white);font-family:"Roboto",Arial,sans-serif;color:var(--text)}
.abs{position:absolute}
h1,h2,h3{font-family:"Poppins",Arial,sans-serif;color:var(--ink);font-weight:700}
.accent{color:var(--blue)}
.btn{display:inline-flex;align-items:center;justify-content:center;height:36px;padding:0 16px;border-radius:18px;font:700 12px "Roboto",Arial,sans-serif;text-transform:uppercase;letter-spacing:.2px;text-decoration:none;border:2px solid var(--blue)}
.btn-solid{background:var(--blue);color:#fff}
.btn-ghost{background:#fff;color:var(--blue)}
.btn-white{background:#fff;color:var(--blue);border-color:#fff}
.btn-outline-light{background:transparent;color:#fff;border-color:#fff}
.deco-circle{position:absolute;border-radius:50%;background:var(--blue-soft)}
.dot-field{position:absolute;border-radius:8px;background:var(--dots);opacity:.55}

/* header */
.site-header{position:absolute;left:0;top:0;width:1200px;height:95px}
.brand{position:absolute;left:143px;top:26px;font:700 34px "Roboto",Arial,sans-serif;color:var(--blue);letter-spacing:-.5px}
.main-nav{position:absolute;left:384px;top:37px;display:flex;gap:34px;font-size:15px;color:#333}
.main-nav a{color:inherit;text-decoration:none}
.main-nav .current{position:relative}
.main-nav .current::after{content:"";position:absolute;left:0;right:0;bottom:-8px;height:2px;background:var(--blue)}
.search-icon{position:absolute;left:884px;top:38px}
.header-cta{position:absolute;left:922px;top:29px;height:36px;padding:0 16px}

/* hero */
.hero-title{position:absolute;left:0;width:1200px;top:140px;text-align:center;font-size:46px;letter-spacing:-.5px}
.hero-lead{position:absolute;left:250px;width:700px;top:224px;text-align:center;font-size:21px;line-height:31px;color:#333}
.hero-actions{position:absolute;left:467px;top:316px;display:flex;gap:6px}
.hero-actions .btn{width:130px}

/* app mockup */
.app{position:absolute;background:#fff;border-radius:20px;overflow:hidden;box-shadow:0 10px 40px rgba(20,40,80,.18)}
.app-side{position:absolute;left:0;top:0;bottom:0;width:36px;background:var(--navy)}
.side-logo{position:absolute;left:10px;top:10px;width:16px;height:16px;background:var(--green);border-radius:3px}
.side-icon{position:absolute;left:12px;width:12px;height:10px;border:2px solid #c7ced8;border-radius:2px}
.entry-main{position:absolute;left:36px;top:0;right:0;bottom:0}
.entry-title{position:absolute;left:63px;top:13px;font:700 14px "Roboto",Arial,sans-serif;color:var(--ink)}
.entry-meta{position:absolute;left:63px;top:42px;display:flex;align-items:center;gap:10px;font-size:10px;color:#333}
.tag{background:var(--green);color:#fff;font-size:9px;font-weight:700;padding:2px 8px;border-radius:8px}
.col{position:absolute;top:84px;bottom:-4px;width:227px;border:1px solid var(--line);border-radius:4px 4px 0 0}
.col-head{position:absolute;left:12px;top:12px;font-size:9px;color:#333;display:flex;align-items:center;gap:6px}
.col-head i{width:8px;height:8px;background:#3b6fd0;border-radius:2px;display:block}
.editor{position:absolute;left:12px;right:12px;top:42px;bottom:0;border:1px solid var(--line)}
.toolbar{height:34px;border-bottom:1px solid var(--line);padding:5px 8px;font-size:8px;color:#444;line-height:12px}
.editor ul{padding:10px 10px 0 26px;font-size:11px;line-height:15.5px;color:#222}

/* hero wave */
.hero-wave{position:absolute;left:0;top:0}

/* what didn't go well */
.wdgw-title{position:absolute;left:146px;top:918px;font-size:44px;color:#fff}
.wdgw-sub{position:absolute;left:146px;top:984px;font-size:23px;color:#fff}
.wdgw-text{position:absolute;left:146px;top:1030px;width:418px;font-size:15.5px;line-height:24.8px;color:#fff;text-align:justify}
.wdgw-btn{position:absolute;left:141px;top:1206px;width:140px;height:42px;border-radius:21px}
.feature-card{position:absolute;background:#fff;border-radius:8px;text-align:center;padding:0 36px}
.feature-card.active{border:3px solid var(--blue);box-shadow:0 10px 30px rgba(10,60,140,.15)}
.feature-card.plain{box-shadow:0 8px 30px rgba(20,40,80,.14)}
.feature-card svg{display:block;margin:0 auto}
.feature-card h3{font:500 19px "Roboto",Arial,sans-serif;color:var(--ink);margin-top:16px}
.feature-card p{font-size:13px;line-height:20.6px;color:#666;text-align:justify;text-align-last:center;margin-top:16px}
.feature-card .btn{width:132px;margin-top:20px}

/* partners */
.partners-title{position:absolute;left:0;width:1200px;top:1530px;text-align:center;font-size:44px}
.partner-row{position:absolute;left:190px;top:1650px;width:830px;display:flex;justify-content:space-around;align-items:center;height:30px}
.partner-row span{font:700 17px "Roboto",Arial,sans-serif;color:#3a3a3a}
.arrow{position:absolute;top:1655px}

/* split sections */
.media-card{position:absolute;left:0;width:504px;background:#fff;border-radius:0 26px 26px 0;box-shadow:0 6px 30px rgba(20,40,80,.13);overflow:hidden}
.split-title{position:absolute;font-size:44px}
.split-text{position:absolute;width:486px;font-size:15.5px;line-height:24.8px;color:#444;text-align:justify}
.split-actions{position:absolute;display:flex;gap:6px}
.split-actions .btn{width:130px}

.list-app{position:absolute;left:670px;top:2344px;width:560px;height:451px;background:#fff;border-radius:16px 0 0 0;box-shadow:0 10px 40px rgba(20,40,80,.16);overflow:hidden}
.list-app .app-side{width:32px}
.add-new{position:absolute;left:94px;top:38px;height:22px;padding:0 10px;border:1px solid var(--line);border-radius:4px;font:500 10px "Roboto",Arial,sans-serif;color:#222;display:flex;align-items:center}
.entry-card{position:absolute;left:90px;width:470px;border:1px solid var(--line);border-radius:6px;padding:12px 16px;font-size:9.5px;line-height:13px;color:#333;background:#fff}
.entry-card b{display:block;font-size:11px;color:#111;margin-bottom:6px}
.entry-card em{display:block;font-style:normal;color:var(--muted);font-size:8.5px;margin:3px 0 2px}

.chart-art{position:absolute;left:46px;top:50px;width:388px;height:356px;border-radius:6px;background:linear-gradient(135deg,#f4fbfb 0%,#dff1f3 55%,#c9e6ea 100%)}

/* cta band */
.cta-band{position:absolute;left:12px;top:3410px;width:1175px;height:329px;border-radius:165px;background:linear-gradient(100deg,#0a59b8 0%,#0747a0 100%)}
.cta-title{position:absolute;left:168px;top:118px;font-size:44px;line-height:56px;color:#fff}
.cta-actions{position:absolute;left:740px;top:113px;display:flex;gap:8px}
.cta-actions .btn{width:130px}

/* footer */
.footer-nav{position:absolute;left:0;width:1200px;top:3797px;display:flex;justify-content:center;gap:22px;font:500 16px "Roboto",Arial,sans-serif;color:#222}
.footer-nav .sep{color:#333}
.legal{position:absolute;left:0;width:1200px;top:3848px;text-align:center;font-size:13px;color:#333}
.social{position:absolute;left:0;width:1200px;top:3914px;display:flex;justify-content:center;gap:22px}
.social span{display:flex;align-items:center;gap:6px;font:500 14px "Roboto",Arial,sans-serif;color:var(--blue-deep)}
.social span::before{content:"";width:22px;height:22px;border-radius:50%;background:var(--blue-deep)}
</style>
</head>
<body>

<!-- decorative backgrounds -->
<div class="deco-circle" style="left:62px;top:348px;width:156px;height:156px"></div>
<div class="dot-field" role="img" aria-label="dot pattern" style="left:100px;top:334px;width:120px;height:110px"></div>
<div class="deco-circle" style="left:948px;top:732px;width:182px;height:182px"></div>
<div class="dot-field" role="img" aria-label="dot pattern" style="left:968px;top:760px;width:120px;height:138px"></div>

<svg class="hero-wave" width="1200" height="1480" viewBox="0 0 1200 1480" aria-hidden="true">
  <defs><linearGradient id="waveFill" x1="0" y1="0" x2="1" y2="1"><stop offset="0" stop-color="#0a5bba"/><stop offset="1" stop-color="#0645a0"/></linearGradient></defs>
  <path d="M0 800 C120 740 300 690 520 660 C760 640 900 700 940 820 C960 900 880 960 875 1060 C870 1200 905 1330 905 1434 C760 1432 620 1405 470 1398 C300 1390 150 1402 0 1410 Z" fill="url(#waveFill)"/>
</svg>
<div class="dot-field" role="img" aria-label="dot pattern" style="left:862px;top:1008px;width:120px;height:110px;opacity:.45"></div>

<!-- header -->
<header class="site-header">
  <div class="brand">Zestora</div>
  <nav class="main-nav">
    <a class="current" href="#">Home</a><a href="#">Features</a><a href="#">Our App</a><a href="#">Resources</a><a href="#">Pricing</a><a href="#">Contact</a>
  </nav>
  <svg class="search-icon" width="16" height="16" viewBox="0 0 16 16" aria-label="Search"><circle cx="6.5" cy="6.5" r="4.8" fill="none" stroke="#222" stroke-width="2.2"/><path d="M10 10l4.5 4.5" stroke="#222" stroke-width="2.4" stroke-linecap="round"/></svg>
  <a class="btn btn-solid header-cta" href="#">Request a demo</a>
</header>

<!-- hero -->
<h1 class="hero-title">Organize your <span class="accent">work and life</span>, finally.</h1>
<p class="hero-lead">At vero eos et accusamus et iusto odio dignissimos ducimus qui blanditiis p iusto ocimus qui blanditiis praesentium</p>
<div class="hero-actions"><a class="btn btn-solid" href="#">Request a demo</a><a class="btn btn-ghost" href="#">How it works</a></div>

<div class="app" style="left:144px;top:392px;width:905px;height:453px">
  <div class="app-side"><div class="side-logo"></div><div class="side-icon" style="top:48px"></div><div class="side-icon" style="top:72px"></div><div class="side-icon" style="top:96px"></div></div>
  <div class="entry-main">
    <div class="entry-title">Entry</div>
    <div class="entry-meta"><span>▦ Thu Aug 22 2024 ⌄</span><span class="tag">Gym</span></div>
    <div class="col" style="left:63px"><div class="col-head"><i></i>What Went Well?</div><div class="editor"><div class="toolbar">Normal ⇕ &nbsp; <b>B</b> <i>I</i> <u>U</u> S ”<br>☰ ☰ ☰ ☰ &nbsp;T</div><ul><li>Completed all scheduled workouts this week.</li><li>Increased bench press weight by 10 pounds.</li><li>Maintained consistent energy levels throughout sessions.</li></ul></div></div>
    <div class="col" style="left:320px"><div class="col-head"><i></i>What Didn't Go Well?</div><div class="editor"><div class="toolbar">Normal ⇕ &nbsp; <b>B</b> <i>I</i> <u>U</u> S ”<br>☰ ☰ ☰ ☰ &nbsp;T</div><ul><li>Struggled with form on deadlifts, leading to lower back discomfort.</li><li>Missed two stretching sessions after workouts.</li><li>Skipped meal prep, resulting in inconsistent nutrition.</li></ul></div></div>
    <div class="col" style="left:578px"><div class="col-head"><i></i>Things To Try</div><div class="editor"><div class="toolbar">Normal ⇕ &nbsp; <b>B</b> <i>I</i> <u>U</u> S ”<br>☰ ☰ ☰ ☰ &nbsp;T</div><ul><li>Focus on deadlift form by lowering the weight and reviewing proper technique.</li><li>Set reminders for post-workout stretching to prevent muscle tightness.</li><li>Dedicate Sunday evenings to meal prep to ensure a balanced diet.</li></ul></div></div>
  </div>
</div>

<!-- what didn't go well -->
<h2 class="wdgw-title">What Didn't Go Well</h2>
<p class="wdgw-sub">At vero eos et accusamus et iusto odio</p>
<p class="wdgw-text">At vero eos et accusamus et iusto odio dignissimos ducimus qui blanditiis praesentium voluptatum deleniti atque corrupti quos dolores et quas molestias excepturi sint occaecati cupiditate non provident, similique sunt in culpa qui officia deserunt mollitia animi, id est laborum et dolorum fuga. Et harum quidem rerum facilis est et expedita distinctio.</p>
<a class="btn btn-white wdgw-btn" href="#">Request a demo</a>

<article class="feature-card active" style="left:614px;top:1038px;width:290px;height:398px;padding-top:34px">
  <svg width="64" height="66" viewBox="0 0 64 66" aria-hidden="true"><rect x="10" y="6" width="36" height="50" rx="4" fill="none" stroke="#0b57b7" stroke-width="2.4"/><rect x="20" y="2" width="16" height="8" rx="2" fill="#fff" stroke="#0b57b7" stroke-width="2.4"/><path d="M16 22l3 3 5-5M16 34l3 3 5-5" stroke="#0b57b7" stroke-width="2.2" fill="none"/><path d="M28 23h12M28 35h12M16 46h24" stroke="#0b57b7" stroke-width="2.2"/><path d="M40 56l16-16 4 4-16 16-6 2z" fill="#fff" stroke="#0b57b7" stroke-width="2.2"/></svg>
  <h3>Nam libero tempore</h3>
  <p>At vero eos et accusamus et iusto odio os ducimus qui blanditiis praesentium voluptatum deleniti atque colores et quas At vero eos et accusamus et iusto odio os ducimus qui blanditiis</p>
  <a class="btn btn-solid" href="#">Read more</a>
</article>
<article class="feature-card plain" style="left:924px;top:1066px;width:290px;height:394px;padding-top:34px">
  <svg width="66" height="66" viewBox="0 0 66 66" aria-hidden="true"><rect x="14" y="14" width="38" height="38" rx="4" fill="none" stroke="#0b57b7" stroke-width="2.4"/><path d="M22 4v10M33 4v10M44 4v10M22 52v10M33 52v10M44 52v10M4 22h10M4 33h10M4 44h10M52 22h10M52 33h10M52 44h10" stroke="#0b57b7" stroke-width="2.2"/><text x="33" y="40" text-anchor="middle" font-family="Roboto,Arial,sans-serif" font-size="17" font-weight="500" fill="#0b57b7">AI</text></svg>
  <h3>Nam libero tempore</h3>
  <p>At vero eos et accusamus et iusto odio os ducimus qui blanditiis praesentium voluptatum deleniti atque colores et quas At vero eos et accusamus et iusto odio os ducimus qui blanditiis</p>
  <a class="btn btn-solid" href="#">Read more</a>
</article>

<!-- partners -->
<h2 class="partners-title">Our <span class="accent">Partners</span></h2>
<svg class="arrow" style="left:118px" width="34" height="20" viewBox="0 0 34 20" aria-label="Previous"><path d="M32 10H3M11 2L3 10l8 8" fill="none" stroke="#222" stroke-width="2"/></svg>
<div class="partner-row"><span>Halvorn</span><span>Drawly</span><span>Fizzco</span><span>Oxenta</span><span>Lumagate</span><span>Carrova</span><span>Bexda</span></div>
<svg class="arrow" style="left:1048px" width="34" height="20" viewBox="0 0 34 20" aria-label="Next"><path d="M2 10h29M23 2l8 8-8 8" fill="none" stroke="#222" stroke-width="2"/></svg>

<!-- what went well -->
<div class="deco-circle" style="left:-42px;top:1712px;width:178px;height:178px"></div>
<div class="dot-field" role="img" aria-label="dot pattern" style="left:424px;top:2180px;width:118px;height:118px"></div>
<div class="media-card" style="top:1806px;height:449px">
  <div class="app" style="left:-10px;top:80px;width:905px;height:453px;transform:scale(.55);transform-origin:0 0;box-shadow:none;border-radius:0">
    <div class="app-side"><div class="side-logo"></div><div class="side-icon" style="top:48px"></div><div class="side-icon" style="top:72px"></div><div class="side-icon" style="top:96px"></div></div>
    <div class="entry-main">
      <div class="entry-title">Entry</div>
      <div class="entry-meta"><span>▦ Thu Aug 22 2024 ⌄</span><span class="tag">Gym</span></div>
      <div class="col" style="left:63px;bottom:20px"><div class="col-head"><i></i>What Went Well?</div><div class="editor"><div class="toolbar">Normal ⇕ &nbsp; <b>B</b> <i>I</i> <u>U</u> S ”<br>☰ ☰ ☰ ☰ &nbsp;T</div><ul><li>Completed all scheduled workouts this week.</li><li>Increased bench press weight by 10 pounds.</li><li>Maintained consistent energy levels throughout sessions.</li></ul></div></div>
      <div class="col" style="left:320px;bottom:20px"><div class="col-head"><i></i>What Didn't Go Well?</div><div class="editor"><div class="toolbar">Normal ⇕ &nbsp; <b>B</b> <i>I</i> <u>U</u> S ”<br>☰ ☰ ☰ ☰ &nbsp;T</div><ul><li>Struggled with form on deadlifts, leading to lower back discomfort.</li><li>Missed two stretching sessions after workouts.</li><li>Skipped meal prep, resulting in inconsistent nutrition.</li></ul></div></div>
      <div class="col" style="left:578px;bottom:20px"><div class="col-head"><i></i>Things To Try</div><div class="editor"><div class="toolbar">Normal ⇕ &nbsp; <b>B</b> <i>I</i> <u>U</u> S ”<br>☰ ☰ ☰ ☰ &nbsp;T</div><ul><li>Focus on deadlift form by lowering the weight and reviewing proper technique.</li><li>Set reminders for post-workout stretching to prevent muscle tightness.</li><li>Dedicate Sunday evenings to meal prep to ensure a balanced diet.</li></ul></div></div>
    </div>
  </div>
</div>
<h2 class="split-title" style="left:570px;top:1852px">What <span class="accent">Went Well</span></h2>
<p class="split-text" style="left:571px;top:1934px">At vero eos et accusamus et iusto odio dignissimos ducimus qui blanditiis praesentium voluptatum deleniti atque corrupti quos dolores et quas molestias excepturi sint occaecati cupiditate non provident, similique sunt in culpa qui officia deserunt mollitia animi, id est laborum et dolorum fuga. Et harum quidem rerum facilis est et expedita distinctio. Nam libero tempore, cum soluta nobis est eligendi optio cumque nihil impedit quo</p>
<div class="split-actions" style="left:572px;top:2111px"><a class="btn btn-solid" href="#">Request a demo</a><a class="btn btn-ghost" href="#">Read more</a></div>

<!-- things to try -->
<div class="deco-circle" style="left:1130px;top:2240px;width:140px;height:140px"></div>
<div class="dot-field" role="img" aria-label="dot pattern" style="left:1064px;top:2284px;width:106px;height:56px"></div>
<div class="dot-field" role="img" aria-label="dot pattern" style="left:634px;top:2718px;width:118px;height:100px"></div>
<h2 class="split-title" style="left:144px;top:2392px">Things <span class="accent">To Try</span></h2>
<p class="split-text" style="left:145px;top:2470px">At vero eos et accusamus et iusto odio dignissimos ducimus qui blanditiis praesentium voluptatum deleniti atque corrupti quos dolores et quas molestias excepturi sint occaecati cupiditate non provident, similique sunt in culpa qui officia deserunt mollitia animi, id est laborum et dolorum fuga. Et harum quidem rerum facilis est et expedita distinctio. Nam libero tempore, cum soluta nobis est eligendi optio cumque nihil impedit quo</p>
<div class="split-actions" style="left:144px;top:2649px"><a class="btn btn-solid" href="#">Request a demo</a><a class="btn btn-ghost" href="#">Read more</a></div>

<div class="list-app">
  <div class="app-side"><div class="side-logo" style="left:8px"></div><div class="side-icon" style="left:10px;top:46px"></div><div class="side-icon" style="left:10px;top:68px"></div><div class="side-icon" style="left:10px;top:90px"></div></div>
  <div class="add-new">+ Add New</div>
  <div class="entry-card" style="top:74px;height:288px">
    <b>Thu Aug 22 2024</b>
    <em>What Went Well</em>
    Completed all scheduled workouts this week.<br>Increased bench press weight by 10 pounds.<br>Maintained consistent energy levels throughout sessions.
    <em>What Didn't Go Well</em>
    Struggled with form on deadlifts, leading to lower back discomfort.<br>Missed two stretching sessions after workouts.<br>Skipped meal prep, resulting in inconsistent nutrition.
    <em>Things To Try</em>
    Focus on deadlift form by lowering the weight and reviewing proper technique.<br>Set reminders for post-workout stretching to prevent muscle tightness.<br>Dedicate Sunday evenings to meal prep to ensure a balanced diet.
  </div>
  <div class="entry-card" style="top:384px;height:90px">
    <b>Tue Aug 20 2024</b>
    <em>What Went Well</em>
    Achieved a personal best in squats, adding 15 pounds.<br>Successfully integrated HIIT into cardio sessions.
  </div>
</div>

<!-- ai coach -->
<div class="dot-field" role="img" aria-label="dot pattern" style="left:0;top:2814px;width:112px;height:60px"></div>
<div class="dot-field" role="img" aria-label="dot pattern" style="left:424px;top:3258px;width:118px;height:112px"></div>
<div class="media-card" style="top:2880px;height:450px">
  <div class="chart-art" role="img" aria-label="Dashboard of journal insight charts: bar, area, line and progress charts in soft blue and teal"></div>
</div>
<h2 class="split-title" style="left:570px;top:2926px">AI <span class="accent">Coach</span></h2>
<p class="split-text" style="left:571px;top:3006px">At vero eos et accusamus et iusto odio dignissimos ducimus qui blanditiis praesentium voluptatum deleniti atque corrupti quos dolores et quas molestias excepturi sint occaecati cupiditate non provident, similique sunt in culpa qui officia deserunt mollitia animi, id est laborum et dolorum fuga. Et harum quidem rerum facilis est et expedita distinctio. Nam libero tempore, cum soluta nobis est eligendi optio cumque nihil impedit quo</p>
<div class="split-actions" style="left:572px;top:3185px"><a class="btn btn-solid" href="#">Request a demo</a><a class="btn btn-ghost" href="#">Read more</a></div>

<!-- cta -->
<div class="deco-circle" style="left:1024px;top:3372px;width:170px;height:170px"></div>
<div class="dot-field" role="img" aria-label="dot pattern" style="left:1092px;top:3418px;width:84px;height:92px"></div>
<section class="cta-band">
  <h2 class="cta-title">Deliver your best work<br>With Zestora</h2>
  <div class="cta-actions"><a class="btn btn-outline-light" href="#">Get started</a><a class="btn btn-white" href="#">Read more</a></div>
</section>

<!-- footer -->
<div class="deco-circle" style="left:-56px;top:3858px;width:158px;height:158px"></div>
<div class="dot-field" role="img" aria-label="dot pattern" style="left:0;top:3928px;width:104px;height:66px"></div>
<nav class="footer-nav"><span>HOME</span><span class="sep">/</span><span>FEATURES</span><span class="sep">/</span><span>OUR APP</span><span class="sep">/</span><span>RESOURCES</span><span class="sep">/</span><span>PRICING</span><span class="sep">/</span><span>CONTACT</span></nav>
<p class="legal">© 2024 Zestora . All Rights Reserved &nbsp;|&nbsp; Terms and privacy &nbsp;|&nbsp; Privacy policy</p>
<div class="social"><span>Picto</span><span>Facet</span><span>Chirp</span><span>Vidora</span></div>

</body>
</html>
```